Pyschiatry Experts need Marketing Campaign

Ad(s) developed for print advertising sharing our purpose and services, highlighting our medical care providers. Must be welcoming and inviting while displaying a high level of professionalism expected from a physician's office.

Target Market(s)

Local community

Industry/Entity Type

Psychiatry (Healthcare)

Requirements
Must have
• Staff pictures, 'Medication Management Experts', 'Prompt Appointments', 'ADD/ADHD, Bipolar Disorder, Depression, Anxiety, Schizophrenia, Grief Reaction and others' 'Virtual and In-Person Visits'
Nice to have
• Address: 412 E Marlowe Coeur d'Alene Phone (208)555-7193 website: BrightLoftCare.com Hours: Mon - Thur 7am - 6pm

```html
<!DOCTYPE html>
<html lang="en">
<head>
<meta charset="utf-8">
<title>Brightloft Care – Mental Health Providers Flyer</title>
<link href="https://fonts.googleapis.com/css2?family=Roboto:wght@400;500;700;900&family=Roboto+Condensed:wght@400;700&family=Arimo:wght@400;700&display=swap" rel="stylesheet">
<style>
  :root{
    --stage:#bdbdbd;
    --paper:#ffffff;
    --cream:#eeede0;
    --ink:#1f3a22;
    --accent:#8db43a;
    --lime:#b5dc5a;
    --deep:#1d3d23;
    --photo-a:#e4e1d9;
    --photo-b:#bdb8ad;
    --portrait-a:#5c646d;
    --portrait-b:#272b30;
    --icon1:#7a62cf;
    --icon2:#3f77d8;
    --icon3:#8a5a16;
    --icon4:#1d3d23;
  }
  *{box-sizing:border-box;margin:0;padding:0}
  html,body{width:1200px;height:866px;overflow:hidden;background:var(--stage)}
  body{position:relative;font-family:"Arimo",Arial,sans-serif;color:#222}

  .flyer{position:absolute;top:63.5px;width:522px;height:738px;background:var(--paper);overflow:hidden}
  .flyer--color{left:65px}
  .flyer--mono{left:617px;
    --cream:#efefef;--ink:#4a4a4a;--accent:#8f8f8f;--lime:#d4d4d4;--deep:#5b5b5b;
    --photo-a:#e2e2e2;--photo-b:#b5b5b5;--portrait-a:#8a8a8a;--portrait-b:#2e2e2e;
    --icon1:#8d8d8d;--icon2:#8d8d8d;--icon3:#8d8d8d;--icon4:#3d3d3d}

  .upper{position:absolute;left:0;top:0;width:522px;height:525px;background:var(--cream)}
  .hero-photo{position:absolute;left:294px;top:0;width:228px;height:221px;
    background:linear-gradient(180deg,var(--photo-a),var(--photo-b))}
  .headline{position:absolute;left:30px;top:33px;font-family:"Roboto",sans-serif;font-weight:700;font-size:36px;line-height:37px;color:var(--ink);letter-spacing:-.2px}
  .services{position:absolute;left:32px;top:150px;font-family:"Roboto",sans-serif;font-size:13.4px;line-height:16px;color:#1b1b1b}
  .band{position:absolute;left:0;top:191px;width:294px;height:30px;background:linear-gradient(90deg,var(--deep) 0,var(--deep) 30%,var(--lime) 100%);
    color:#fff;font-family:"Roboto",sans-serif;font-size:15.4px;line-height:30px;padding-left:33px}

  .provider{position:absolute;top:227px;width:106px}
  .provider__photo{height:123px;background:linear-gradient(180deg,var(--portrait-a),var(--portrait-b))}
  .provider__name{height:28px;background:var(--lime);text-align:center;font-family:"Roboto",sans-serif;font-size:10.5px;line-height:11.5px;padding-top:3px;color:#111}
  .provider__name b{font-family:"Roboto Condensed",sans-serif;font-weight:700;font-size:11px}
  .provider__bio{margin-top:6px;font-size:8.1px;line-height:9.5px;text-align:center;color:#222}

  .scope{position:absolute;left:33px;top:540px;width:312px;font-size:9.7px;line-height:11.5px;color:#111}
  .scope strong{color:var(--ink);font-size:9.5px}
  .portal{position:absolute;left:33px;top:601px;width:315px;height:66px;border:1px solid #555;border-radius:3px}
  .portal__title{text-align:center;font-family:"Roboto Condensed",sans-serif;font-size:10.5px;margin-top:3px;color:#111}
  .portal__item{position:absolute;top:19px;text-align:center;font-size:8.4px;color:#111;white-space:nowrap}
  .portal__item svg{display:block;margin:0 auto 4px}
  .portal__rule{position:absolute;top:19px;width:1px;height:42px;background:#bbb}
  .hours{position:absolute;left:31px;top:673px;font-family:"Roboto",sans-serif;font-size:16px;color:#222}
  .hours span{color:var(--accent);font-weight:500}

  .divider{position:absolute;left:357px;top:538px;width:1px;height:148px;background:#ccc}
  .contact{position:absolute;left:362px;top:542px;width:160px;text-align:center;font-family:"Roboto",sans-serif;color:#222}
  .brand{display:flex;flex-direction:column;align-items:center}
  .brand__dot{width:34px;height:34px;border-radius:50%;background:var(--accent)}
  .brand__name{margin-top:5px;font-size:14.5px;font-weight:500;letter-spacing:1.2px;color:var(--accent)}
  .contact__label{margin-top:12px;font-size:8.5px;font-weight:700;color:var(--accent)}
  .contact__lines{margin-top:11px;font-size:8.6px;line-height:10.5px}
  .contact__row{margin-top:5px;font-size:8.6px}
  .contact__row span{color:var(--accent);font-weight:700}

  .footer{position:absolute;left:0;bottom:0;width:522px;height:41px;background:linear-gradient(90deg,var(--deep) 0,var(--deep) 25%,var(--lime) 100%);
    color:#fff;text-align:center;font-family:"Roboto",sans-serif;font-size:19px;line-height:41px}
  .flyer--mono .footer{background:linear-gradient(90deg,#555 0,#5d5d5d 40%,#c9c9c9 100%)}
  .flyer--mono .band{background:linear-gradient(90deg,#5a5a5a,#8a8a8a 70%,#d5d5d5)}
</style>
</head>
<body>

<section class="flyer flyer--color">
  <div class="upper"></div>
  <div class="hero-photo" role="img" aria-label="Photo of a smiling woman seated on a sofa, looking at her phone"></div>
  <h1 class="headline">Helping Bodies<br>Helping Minds<br>Helping you</h1>
  <p class="services">Mental Health and Psychiatry Services<br>Migraine and Neurospasticity Intervention</p>
  <div class="band">Meet Our Mental Health Providers</div>

  <article class="provider" style="left:33px">
    <div class="provider__photo" role="img" aria-label="Studio portrait of provider Evan Marsh"></div>
    <div class="provider__name"><b>Evan Marsh,</b><br>PMHNP - BC</div>
    <p class="provider__bio">Before entering into healthcare, Evan spent years in academia researching foundational cellular and molecular biology mechanisms along with genetics that has provided a strong basis for understanding complex psychiatric conditions and the medications used in behavioral health. Evan cares for teenagers thru adult patients populations.</p>
  </article>
  <article class="provider" style="left:151px">
    <div class="provider__photo" role="img" aria-label="Studio portrait of provider Curtis Vale"></div>
    <div class="provider__name"><b>Curtis Vale,</b><br>PMHNP - BC</div>
    <p class="provider__bio">With a former career in the inpatient behavioral health environment, Curtis is excited to share her experience and passion for mental health in an outpatient setting. Her practice cares for teenagers to adults in all aspects of psychiatry and mental wellness.</p>
  </article>
  <article class="provider" style="left:268px">
    <div class="provider__photo" role="img" aria-label="Studio portrait of provider Dale Prewitt"></div>
    <div class="provider__name"><b>Dale Prewitt</b><br>PMHNP - BC</div>
    <p class="provider__bio">Formally from North Idaho and having moved back to this area, Dale brings several years of pediatric and adolescent experience to Brightloft Care. Outside of work, Dale enjoys spending time with his wife and two children, exploring various outdoor pursuits including backpacking, fishing, and all things Bigfoot.</p>
  </article>
  <article class="provider" style="left:383px">
    <div class="provider__photo" role="img" aria-label="Studio portrait of provider Helen Ashcombe"></div>
    <div class="provider__name"><b>Helen Ashcombe,</b><br>PMHNP-BC, DNP</div>
    <p class="provider__bio">Dr. Helen Ashcombe is Board Certified in Geriatric and Adult Psychiatric Medicine. She has practiced Psychiatry for over 30 years and has extensive experience in the diagnosis and treatment of major mental illnesses. Her passion for mental wellness values the long term relationship with the adult and geriatric patient.</p>
  </article>

  <p class="scope"><strong>Bringing comprehensive evaluation, medication management and psychotherapy to the full spectrum of mental health disorders including:</strong><br>Minor, moderate and major depression, bipolar disorder, ADD/ADHD, anxiety, schizophrenia, stress or grief reactions, and others.</p>

  <div class="portal">
    <p class="portal__title">We know your days are busy!&nbsp; Use our Patient Portal for:</p>
    <div class="portal__item" style="left:4px;width:76px"><svg width="26" height="26" viewBox="0 0 26 26"><circle cx="13" cy="13" r="13" fill="var(--icon1)"/><circle cx="13" cy="13" r="5" fill="none" stroke="#fff" stroke-width="1.2"/></svg>Online Massaging</div>
    <span class="portal__rule" style="left:82px"></span>
    <div class="portal__item" style="left:86px;width:94px"><svg width="26" height="26" viewBox="0 0 26 26"><circle cx="13" cy="13" r="13" fill="var(--icon2)"/><path d="M10 17l1-3 5-5 2 2-5 5z" fill="none" stroke="#fff" stroke-width="1.2"/></svg>Prescription Renewal</div>
    <span class="portal__rule" style="left:183px"></span>
    <div class="portal__item" style="left:187px;width:64px"><svg width="26" height="26" viewBox="0 0 26 26"><circle cx="13" cy="13" r="13" fill="var(--icon3)"/><rect x="7.5" y="10" width="8" height="6" fill="none" stroke="#fff" stroke-width="1.2"/><path d="M15.5 12l3-2v6l-3-2" fill="none" stroke="#fff" stroke-width="1.2"/></svg>Virtual Visits</div>
    <span class="portal__rule" style="left:253px"></span>
    <div class="portal__item" style="left:256px;width:56px;top:23px"><svg width="26" height="26" viewBox="0 0 26 26"><circle cx="13" cy="13" r="13" fill="var(--icon4)"/><rect x="8" y="10" width="10" height="7" fill="none" stroke="#fff" stroke-width="1.2"/><circle cx="13" cy="13.5" r="1.5" fill="#fff"/></svg>Pay Your Bill</div>
  </div>
  <p class="hours"><span>Hours:</span> Mon - Thur 7am - 6pm</p>

  <span class="divider"></span>
  <div class="contact">
    <div class="brand"><span class="brand__dot"></span><span class="brand__name">BRIGHTLOFT CARE</span></div>
    <p class="contact__label">Contact us:</p>
    <p class="contact__lines">Brightloft Care<br>412 E Marlowe Coeur d'Alene</p>
    <p class="contact__row"><span>Phone:</span> (208)555-7193</p>
    <p class="contact__row"><span>Website:</span> BrightLoftCare.com</p>
  </div>

  <div class="footer">WE CARE FOR YOUR HEALTH</div>
</section>

<section class="flyer flyer--mono">
  <div class="upper"></div>
  <div class="hero-photo" role="img" aria-label="Black and white photo of a smiling woman seated on a sofa, looking at her phone"></div>
  <h1 class="headline">Helping Bodies<br>Helping Minds<br>Helping you</h1>
  <p class="services">Mental Health and Psychiatry Services<br>Migraine and Neurospasticity Intervention</p>
  <div class="band">Meet Our Mental Health Providers</div>

  <article class="provider" style="left:33px">
    <div class="provider__photo" role="img" aria-label="Black and white studio portrait of provider Evan Marsh"></div>
    <div class="provider__name"><b>Evan Marsh,</b><br>PMHNP - BC</div>
    <p class="provider__bio">Before entering into healthcare, Evan spent years in academia researching foundational cellular and molecular biology mechanisms along with genetics that has provided a strong basis for understanding complex psychiatric conditions and the medications used in behavioral health. Evan cares for teenagers thru adult patients populations.</p>
  </article>
  <article class="provider" style="left:151px">
    <div class="provider__photo" role="img" aria-label="Black and white studio portrait of provider Curtis Vale"></div>
    <div class="provider__name"><b>Curtis Vale,</b><br>PMHNP - BC</div>
    <p class="provider__bio">With a former career in the inpatient behavioral health environment, Curtis is excited to share her experience and passion for mental health in an outpatient setting. Her practice cares for teenagers to adults in all aspects of psychiatry and mental wellness.</p>
  </article>
  <article class="provider" style="left:268px">
    <div class="provider__photo" role="img" aria-label="Black and white studio portrait of provider Dale Prewitt"></div>
    <div class="provider__name"><b>Dale Prewitt</b><br>PMHNP - BC</div>
    <p class="provider__bio">Formally from North Idaho and having moved back to this area, Dale brings several years of pediatric and adolescent experience to Brightloft Care. Outside of work, Dale enjoys spending time with his wife and two children, exploring various outdoor pursuits including backpacking, fishing, and all things Bigfoot.</p>
  </article>
  <article class="provider" style="left:383px">
    <div class="provider__photo" role="img" aria-label="Black and white studio portrait of provider Helen Ashcombe"></div>
    <div class="provider__name"><b>Helen Ashcombe,</b><br>PMHNP-BC, DNP</div>
    <p class="provider__bio">Dr. Helen Ashcombe is Board Certified in Geriatric and Adult Psychiatric Medicine. She has practiced Psychiatry for over 30 years and has extensive experience in the diagnosis and treatment of major mental illnesses. Her passion for mental wellness values the long term relationship with the adult and geriatric patient.</p>
  </article>

  <p class="scope"><strong>Bringing comprehensive evaluation, medication management and psychotherapy to the full spectrum of mental health disorders including:</strong><br>Minor, moderate and major depression, bipolar disorder, ADD/ADHD, anxiety, schizophrenia, stress or grief reactions, and others.</p>

  <div class="portal">
    <p class="portal__title">We know your days are busy!&nbsp; Use our Patient Portal for:</p>
    <div class="portal__item" style="left:4px;width:76px"><svg width="26" height="26" viewBox="0 0 26 26"><circle cx="13" cy="13" r="13" fill="var(--icon1)"/><circle cx="13" cy="13" r="5" fill="none" stroke="#fff" stroke-width="1.2"/></svg>Online Massaging</div>
    <span class="portal__rule" style="left:82px"></span>
    <div class="portal__item" style="left:86px;width:94px"><svg width="26" height="26" viewBox="0 0 26 26"><circle cx="13" cy="13" r="13" fill="var(--icon2)"/><path d="M10 17l1-3 5-5 2 2-5 5z" fill="none" stroke="#fff" stroke-width="1.2"/></svg>Prescription Renewal</div>
    <span class="portal__rule" style="left:183px"></span>
    <div class="portal__item" style="left:187px;width:64px"><svg width="26" height="26" viewBox="0 0 26 26"><circle cx="13" cy="13" r="13" fill="var(--icon3)"/><rect x="7.5" y="10" width="8" height="6" fill="none" stroke="#fff" stroke-width="1.2"/><path d="M15.5 12l3-2v6l-3-2" fill="none" stroke="#fff" stroke-width="1.2"/></svg>Virtual Visits</div>
    <span class="portal__rule" style="left:253px"></span>
    <div class="portal__item" style="left:256px;width:56px;top:23px"><svg width="26" height="26" viewBox="0 0 26 26"><circle cx="13" cy="13" r="13" fill="var(--icon4)"/><rect x="8" y="10" width="10" height="7" fill="none" stroke="#fff" stroke-width="1.2"/><circle cx="13" cy="13.5" r="1.5" fill="#fff"/></svg>Pay Your Bill</div>
  </div>
  <p class="hours"><span>Hours:</span> Mon - Thur 7am - 6pm</p>

  <span class="divider"></span>
  <div class="contact">
    <div class="brand"><span class="brand__dot"></span><span class="brand__name">BRIGHTLOFT CARE</span></div>
    <p class="contact__label">Contact us:</p>
    <p class="contact__lines">Brightloft Care<br>412 E Marlowe Coeur d'Alene</p>
    <p class="contact__row"><span>Phone:</span> (208)555-7193</p>
    <p class="contact__row"><span>Website:</span> BrightLoftCare.com</p>
  </div>

  <div class="footer">WE CARE FOR YOUR HEALTH</div>
</section>

</body>
</html>
```